BUSINESS CARD DESIGN

NAME- DALE VORSKIN
PHONE NUMER - 555- 714-9082
EMAIL- OFFICE@TRV-GROUNDMAKRZ.COM
BACK OF CARD- SPEACIALIZES IN LAND CLEARING, FORESTRY MUCLHING AND EXCAVATION

Contact Information for Business Card

NAME- DALE VORSKIN PHONE NUMER - 555- 714-9082 EMAIL- OFFICE@TRV-GROUNDMAKRZ.COM BACK OF CARD- SPEACIALIZES IN LAND CLEARING , MUCLHING AND EXCAVATION

```html
<!DOCTYPE html>
<html lang="en">
<head>
<meta charset="utf-8">
<title>Business Card – Traverse Groundmakrz</title>
<link href="https://fonts.googleapis.com/css2?family=Montserrat:wght@400;500;700&display=swap" rel="stylesheet">
<style>
  :root {
    --backdrop: #9b9b9b;
    --card-light: #ffffff;
    --card-dark: #050505;
    --accent: #f4b01c;
    --ink: #1a1a1a;
  }
  * { margin: 0; padding: 0; box-sizing: border-box; }
  html, body {
    width: 1093px; height: 1200px; overflow: hidden;
    background: var(--backdrop);
    font-family: 'Montserrat', Arial, sans-serif;
  }
  .card {
    position: absolute; left: 264px; width: 597px; height: 364px;
    box-shadow: 0 1px 3px rgba(0,0,0,0.45);
  }
  .card-front { top: 224px; background: var(--card-light); color: var(--ink); }
  .card-back { top: 615px; height: 367px; background: var(--card-dark); }

  .holder-name {
    position: absolute; left: 35px; top: 50px;
    font-size: 23px; font-weight: 700; color: var(--accent); letter-spacing: 0.3px;
  }
  .holder-title {
    position: absolute; left: 35px; top: 78px; font-size: 14px; font-weight: 500;
  }

  .brand {
    position: absolute; display: flex; flex-direction: column; align-items: center;
    font-weight: 700; text-align: center; letter-spacing: 1px;
  }
  .brand-mark { border-radius: 50%; }
  .brand-front { right: 28px; top: 18px; width: 160px; color: var(--ink); font-size: 13px; line-height: 1.3; }
  .brand-front .brand-mark { width: 80px; height: 80px; border: 3px solid var(--ink); margin-bottom: 12px; }
  .brand-back { left: 0; right: 0; top: 44px; color: var(--accent); font-size: 24px; line-height: 1.3; }
  .brand-back .brand-mark { width: 160px; height: 160px; border: 5px solid var(--accent); margin-bottom: 16px; }

  .services {
    position: absolute; left: 0; right: 0; top: 312px;
    text-align: center; color: var(--accent);
    font-size: 11px; font-weight: 500; letter-spacing: 1px;
  }

  .contact-list { position: absolute; left: 35px; top: 266px; list-style: none; font-size: 14px; font-weight: 500; }
  .contact-list li { display: flex; align-items: center; height: 23.3px; }
  .contact-list svg { width: 13px; height: 13px; margin-right: 7px; fill: var(--accent); }

  .address {
    position: absolute; left: 416px; top: 300px; font-size: 13.5px; font-weight: 500; line-height: 1.2;
    font-style: normal; white-space: nowrap;
  }
</style>
</head>
<body>
  <section class="card card-front">
    <h1 class="holder-name">DALE VORSKIN</h1>
    <p class="holder-title">Managing Director</p>

    <div class="brand brand-front">
      <span class="brand-mark"></span>
      <span>TRAVERSE<br>GROUNDMAKRZ LLC</span>
    </div>

    <ul class="contact-list">
      <li>
        <svg viewBox="0 0 24 24" aria-hidden="true"><path d="M6.6 10.8a15.1 15.1 0 0 0 6.6 6.6l2.2-2.2c.3-.3.7-.4 1-.2 1.1.4 2.3.6 3.6.6.6 0 1 .4 1 1V20c0 .6-.4 1-1 1A17 17 0 0 1 3 4c0-.6.4-1 1-1h3.5c.6 0 1 .4 1 1 0 1.3.2 2.5.6 3.6.1.3 0 .7-.2 1z"/></svg>
        555- 714-9082
      </li>
      <li>
        <svg viewBox="0 0 24 24" aria-hidden="true"><path d="M2 5h20v2l-10 6L2 7z M2 9l10 6 10-6v10H2z"/></svg>
        OFFICE@TRV-GROUNDMAKRZ.COM
      </li>
      <li>
        <svg viewBox="0 0 24 24" aria-hidden="true"><path d="M12 2a10 10 0 1 0 0 20 10 10 0 0 0 0-20zm-1 17.9A8 8 0 0 1 4.1 10l4.9 4.9v1a2 2 0 0 0 2 2zm6.9-2.5a2 2 0 0 0-1.9-1.4h-1v-3a1 1 0 0 0-1-1H8v-2h2a1 1 0 0 0 1-1V7h2a2 2 0 0 0 2-2v-.4a8 8 0 0 1 2.9 12.8z"/></svg>
        WWW.TRV-GROUNDMAKRZ.COM
      </li>
    </ul>

    <address class="address">418 Cedar Ridge Rd, #112<br>Fairmont, OH 43019</address>
  </section>

  <section class="card card-back">
    <div class="brand brand-back">
      <span class="brand-mark"></span>
      <span>TRAVERSE<br>GROUNDMAKRZ LLC</span>
    </div>
    <p class="services">SPECIALIZES IN LAND CLEARING, FORESTRY MULCHING AND EXCAVATION</p>
  </section>
</body>
</html>
```